Young company in the agrifood product sector *

Our company% 26 # 233; t% 26 # 233; Ambrel Crest low% 26 # 233; % 26 # 224; Toulouse et sp% 26 # 233; cialis% 26 # 233; in the packaging and marketing of beehive products, We need a design of% 26 # 39;% 26 # 39;% 26 # 233; label for honey jar of 250g, The% 26 # 233; labels destiny% 26 # 233; the honey jars will be transparent so that the nectar is visible from the front, our Ambrel Crest logo must be% 26 # 234; be located% 26 # 233; above / middle of% 26 # 393% label followed below the appellation, for example Ch% 26 # 226; taignier followed below the country of% 26 # 39; origin France tracking below r% 26 # 233; region of r% 26 # 233; colte Midi-Pyr% 26 # 233; n% 26 # 233; es and below l% 26 # 39;% 26 # 233; label weight 250g and% 26lt;% 26lt;% 26lt; Honey% 26gt;% 26gt; on the% 26 # 39;% 26 # 233; label will be a plus but optional, The dimensions of the% 26 # 39;% 26 # 233; label are the following 6cm x 6cm. The design must inspire quality% 26 # 233; luxury, l% 26 # 39;% 26 # 233; l% 26 # 233; elegance and confidence, these are quality honey% 26 # 233; and rare honeys from around the world which are very expensive. Very important, the honeys have different colors, this can range from white to orange yellow or darker shades of brown% 26 # 234; black, that's why we would like to have at least 3 colors for light honey, medium dark% 26 # 233; and dark% 26 # 233 ;, Regarding the colors you have free choice of course% 26 # 251; r taking into account the colors of the honey which must% 26 # 234; be visible% 26 # 224; through the% 26 # 39;% 26 # 233; transparent label You will find attached the files of our Ambrel Crest logo. 20%% 26 # 224; 40% transparency on the% 26 # 39;% 26 # 233; label would be reasonable but% 26 # 224; you to see which is better, thanks
- Krone one

```html
<!DOCTYPE html>
<html lang="fr">
<head>
<meta charset="utf-8">
<title>Ambrel Crest – Étiquettes Châtaignier 250g</title>
<link rel="stylesheet" href="https://fonts.googleapis.com/css2?family=Montserrat:wght@600;700&display=swap">
<style>
  :root {
    --bg: #f1f2f3;
    --ink-dark: #111111;
    --ink-light: #ffffff;
  }
  * { margin: 0; padding: 0; box-sizing: border-box; }
  html, body { width: 1200px; height: 923px; overflow: hidden; }
  body {
    background: var(--bg);
    font-family: "Montserrat", sans-serif;
    display: flex;
    align-items: center;
    justify-content: center;
  }
  .label-range {
    display: flex;
    gap: 24px;
  }
  .honey-label {
    width: 270px;
    height: 270px;
    border-radius: 10px;
    background: linear-gradient(180deg, var(--honey-light), var(--honey));
    overflow: hidden;
  }
  .honey-label svg { display: block; width: 100%; height: 100%; }

  .label-text { font-family: "Montserrat", sans-serif; font-weight: 700; text-anchor: middle; }
  .brand-name { fill: var(--logo); font-size: 19px; }
  .brand-dot { fill: var(--logo); }
  .shield-part { fill: var(--shape); opacity: var(--shape-opacity); }
  .appellation { fill: var(--shape-text); font-size: 19px; letter-spacing: 0.5px; }
  .origin { fill: var(--shape-text); font-size: 15px; letter-spacing: 1px; }
  .region { fill: var(--shape-text); font-size: 8px; font-weight: 600; }
  .pointer { fill: var(--shape); opacity: var(--shape-opacity); }
  .weight { fill: var(--weight); font-size: 11px; }

  .honey-light-black {
    --honey: #f3a914; --honey-light: #fcc23c;
    --shape: #0d0b08; --shape-opacity: 1; --shape-text: #f5b52a;
    --logo: var(--ink-dark); --weight: var(--ink-dark);
  }
  .honey-light-bronze {
    --honey: #f0a11a; --honey-light: #fbbd45;
    --shape: #a88656; --shape-opacity: 0.85; --shape-text: #e9a930;
    --logo: #fff3da; --weight: #fff3da;
  }
  .honey-medium-silver {
    --honey: #ea6212; --honey-light: #f68f22;
    --shape: #dcd7cf; --shape-opacity: 1; --shape-text: #f07a18;
    --logo: var(--ink-light); --weight: var(--ink-light);
  }
  .honey-dark-white {
    --honey: #c82612; --honey-light: #e0441c;
    --shape: #ffffff; --shape-opacity: 1; --shape-text: #d22a18;
    --logo: var(--ink-light); --weight: var(--ink-light);
  }
</style>
</head>
<body>
  <main class="label-range">
    <article class="honey-label honey-light-black">
      <svg viewBox="0 0 260 260" aria-label="Étiquette Châtaignier, version noire">
        <g class="brand">
          <circle class="brand-dot" cx="60" cy="38" r="6"/>
          <text class="label-text brand-name" x="138" y="45">Ambrel Crest</text>
        </g>
        <path class="shield-part" d="M22,76 Q130,62 238,76 L234,106 Q130,100 26,106 Z"/>
        <text class="label-text appellation" x="130" y="97">Châtaignier</text>
        <path class="shield-part" d="M27,112 Q130,106 233,112 L228,144 Q130,136 32,144 Z"/>
        <text class="label-text origin" x="130" y="133">FRANCE</text>
        <path class="shield-part" d="M40,152 Q130,144 220,152 Q204,190 130,194 Q56,190 40,152 Z"/>
        <text class="label-text region" x="130" y="180">Midi-Pyrénées</text>
        <path class="pointer" d="M122,200 L138,200 L130,209 Z"/>
        <text class="label-text weight" x="130" y="232">250g</text>
      </svg>
    </article>

    <article class="honey-label honey-light-bronze">
      <svg viewBox="0 0 260 260" aria-label="Étiquette Châtaignier, version bronze">
        <g class="brand">
          <circle class="brand-dot" cx="60" cy="38" r="6"/>
          <text class="label-text brand-name" x="138" y="45">Ambrel Crest</text>
        </g>
        <path class="shield-part" d="M22,76 Q130,62 238,76 L234,106 Q130,100 26,106 Z"/>
        <text class="label-text appellation" x="130" y="97">Châtaignier</text>
        <path class="shield-part" d="M27,112 Q130,106 233,112 L228,144 Q130,136 32,144 Z"/>
        <text class="label-text origin" x="130" y="133">FRANCE</text>
        <path class="shield-part" d="M40,152 Q130,144 220,152 Q204,190 130,194 Q56,190 40,152 Z"/>
        <text class="label-text region" x="130" y="180">Midi-Pyrénées</text>
        <path class="pointer" d="M122,200 L138,200 L130,209 Z"/>
        <text class="label-text weight" x="130" y="232">250g</text>
      </svg>
    </article>

    <article class="honey-label honey-medium-silver">
      <svg viewBox="0 0 260 260" aria-label="Étiquette Châtaignier, version argent">
        <g class="brand">
          <circle class="brand-dot" cx="60" cy="38" r="6"/>
          <text class="label-text brand-name" x="138" y="45">Ambrel Crest</text>
        </g>
        <path class="shield-part" d="M22,76 Q130,62 238,76 L234,106 Q130,100 26,106 Z"/>
        <text class="label-text appellation" x="130" y="97">Châtaignier</text>
        <path class="shield-part" d="M27,112 Q130,106 233,112 L228,144 Q130,136 32,144 Z"/>
        <text class="label-text origin" x="130" y="133">FRANCE</text>
        <path class="shield-part" d="M40,152 Q130,144 220,152 Q204,190 130,194 Q56,190 40,152 Z"/>
        <text class="label-text region" x="130" y="180">Midi-Pyrénées</text>
        <path class="pointer" d="M122,200 L138,200 L130,209 Z"/>
        <text class="label-text weight" x="130" y="232">250g</text>
      </svg>
    </article>

    <article class="honey-label honey-dark-white">
      <svg viewBox="0 0 260 260" aria-label="Étiquette Châtaignier, version blanche">
        <g class="brand">
          <circle class="brand-dot" cx="60" cy="38" r="6"/>
          <text class="label-text brand-name" x="138" y="45">Ambrel Crest</text>
        </g>
        <path class="shield-part" d="M22,76 Q130,62 238,76 L234,106 Q130,100 26,106 Z"/>
        <text class="label-text appellation" x="130" y="97">Châtaignier</text>
        <path class="shield-part" d="M27,112 Q130,106 233,112 L228,144 Q130,136 32,144 Z"/>
        <text class="label-text origin" x="130" y="133">FRANCE</text>
        <path class="shield-part" d="M40,152 Q130,144 220,152 Q204,190 130,194 Q56,190 40,152 Z"/>
        <text class="label-text region" x="130" y="180">Midi-Pyrénées</text>
        <path class="pointer" d="M122,200 L138,200 L130,209 Z"/>
        <text class="label-text weight" x="130" y="232">250g</text>
      </svg>
    </article>
  </main>
</body>
</html>
```